4 page brochure for Logistics Company

Need a 4 page brochure (ie folded A3) for a Logistics company.
Service is a virtual network of warehouse and logistics companies.
Style is professional but accessible.
We have logo and styles designed and will upload these.
We have identified example images that could be used in the brochure.
Content will be uploaded also.
Reason: A couple of designers requested more time
Am giving another 24 hours to finalise and will then select most suitable design
Target Market(s)
40 to 60 year old business owners (traditional) - Australian
Industry/Entity Type
It Company
Requirements
Must have
- Professional
Should not have
- Nothing tacky

```html
<!DOCTYPE html>
<html lang="en">
<head>
<meta charset="utf-8">
<title>Team and Route Spread</title>
<link href="https://fonts.googleapis.com/css2?family=Open+Sans:ital,wght@0,300;0,400;0,600;0,700;1,400&display=swap" rel="stylesheet">
<style>
  :root{
    --backdrop:#e6e8ea;
    --paper:#ffffff;
    --brand-blue:#1e7bc0;
    --deep-blue:#1a5aa3;
    --title-blue:#2a6db5;
    --accent-blue:#2f86c6;
    --slate:#72848f;
    --slate-edge:#8a9aa3;
    --white:#ffffff;
    --ink:#4a4f55;
    --map-land:#ede9e0;
    --map-edge:#c9c2d8;
  }
  *{box-sizing:border-box;margin:0;padding:0}
  html,body{width:1200px;height:960px;overflow:hidden;background:var(--backdrop);font-family:"Open Sans",Arial,sans-serif}
  .spread{position:absolute;left:20px;top:70px;width:1252px;height:885px;transform:scale(0.9265);transform-origin:0 0;background:var(--paper);box-shadow:0 6px 24px rgba(0,0,0,.18);overflow:hidden}
  .page{position:absolute;top:0;height:885px;width:626px}
  .page--left{left:0}
  .page--right{left:626px}
  .corner-swoosh{position:absolute;top:0}
  .page--left .corner-swoosh{left:0}
  .page--right .corner-swoosh{right:0}

  .team-title{position:absolute;left:216px;top:22px;font-weight:300;font-size:30px;color:var(--title-blue)}
  .team-intro{position:absolute;left:222px;top:70px;width:380px;font-style:italic;font-size:10.6px;line-height:17.5px;color:var(--ink)}
  .company-heading{position:absolute;left:16px;top:144px;font-weight:300;font-size:16px;color:var(--accent-blue);letter-spacing:.2px}

  .member{position:absolute;left:13px;width:589px;height:209px;background:var(--slate);color:var(--white)}
  .member--one{top:179px}
  .member--two{top:411px}
  .member--three{top:644px}
  .member__strengths{position:absolute;left:20px;top:26px;width:205px;font-size:10.3px;line-height:12.5px}
  .member__strengths h3{font-size:12.5px;font-weight:600;margin-bottom:6px}
  .member__strengths p{margin-bottom:9px}
  .member__strengths h3 + p{margin-bottom:9px}
  .member__strengths p + h3{margin-top:6px}
  .member__profile{position:absolute;left:233px;top:0;width:158px;height:209px;background:var(--brand-blue);text-align:center}
  .member__portrait{position:absolute;left:12px;top:12px;width:136px;height:136px;border-radius:50%;border:5px solid var(--white);background:radial-gradient(circle at 50% 45%,#c9b8a8 0%,#8d8e92 55%,#4d5966 100%)}
  .member__name{position:absolute;left:0;right:0;top:158px;font-size:14px}
  .member__credentials{position:absolute;left:4px;right:4px;top:179px;font-size:10px;line-height:13px}
  .member__highlights{position:absolute;left:399px;top:20px;width:185px;list-style:none;font-size:10.3px;line-height:13px}
  .member__highlights li{position:relative;padding-left:14px;margin-bottom:13px}
  .tick{position:absolute;left:0;top:2px;width:10px;height:10px}

  .route-title{position:absolute;left:0;right:0;top:28px;text-align:center;font-weight:300;font-size:18.5px;color:var(--accent-blue)}
  .route-map{position:absolute;left:48px;top:72px;width:530px;height:455px;border-radius:40% 35% 45% 40%;background:radial-gradient(ellipse at 50% 50%,var(--map-land) 60%,var(--map-edge) 100%);opacity:.95}
  .warehouse-photo{position:absolute;left:0;top:535px;width:626px;height:350px;background:linear-gradient(180deg,#f4f2ee 0%,#d8cdbd 40%,#b89c78 75%,#c8b59a 100%)}
  .site-address{position:absolute;left:0;right:0;top:840px;text-align:center;font-size:16px;color:#2f3338}
</style>
</head>
<body>
<div class="spread">
  <section class="page page--left">
    <svg class="corner-swoosh" width="260" height="110" viewBox="0 0 260 110" aria-hidden="true">
      <path d="M0 0H255C225 20 190 75 120 95C70 108 25 106 0 104Z" fill="#9aa7b0"/>
      <path d="M0 0H205C180 25 150 70 100 90C60 105 25 106 0 104Z" fill="var(--deep-blue)"/>
    </svg>
    <h1 class="team-title">Our team (Who?)</h1>
    <p class="team-intro">With over 30 years or experience in warehouse, logistics and transportation and over 30 years of history in mergers, acquisitions and business sales, the SLL team is uniquely qualified to deliver outcomes to its members.</p>
    <h2 class="company-heading">SOUTHERN LINKED LOGISTICS</h2>

    <article class="member member--one">
      <div class="member__strengths">
        <h3>Logistics industry expertise:</h3>
        <p>Directors have &gt;30 years' experience in warehouse, logistics and transportation</p>
        <h3>Credibility from track record:</h3>
        <p>30 year history in M&amp;A and business sales</p>
        <p>National footprint</p>
        <p>Operates under an AFSL</p>
      </div>
      <div class="member__profile">
        <div class="member__portrait" role="img" aria-label="Portrait photo of Graham Tully"></div>
        <div class="member__name">Graham Tully</div>
        <div class="member__credentials">Bcomm, FAICD, CPA, FCILT</div>
      </div>
      <ul class="member__highlights">
        <li><svg class="tick" viewBox="0 0 10 10"><circle cx="5" cy="5" r="4.3" fill="none" stroke="#fff" stroke-width="1"/><path d="M2.8 5.1L4.4 6.6L7.3 3.4" fill="none" stroke="#fff" stroke-width="1.1"/></svg>30 years' warehouse, logistics, transportation experience in expansion, mergers, acquisitions and divestment</li>
        <li><svg class="tick" viewBox="0 0 10 10"><circle cx="5" cy="5" r="4.3" fill="none" stroke="#fff" stroke-width="1"/><path d="M2.8 5.1L4.4 6.6L7.3 3.4" fill="none" stroke="#fff" stroke-width="1.1"/></svg>Established a national warehousing company</li>
        <li><svg class="tick" viewBox="0 0 10 10"><circle cx="5" cy="5" r="4.3" fill="none" stroke="#fff" stroke-width="1"/><path d="M2.8 5.1L4.4 6.6L7.3 3.4" fill="none" stroke="#fff" stroke-width="1.1"/></svg>Managed sale and acquisition of warehouse business</li>
      </ul>
    </article>

    <article class="member member--two">
      <div class="member__strengths">
        <h3>M&amp;A and advisory expertise:</h3>
        <p>&gt; $10B in combined transaction experience</p>
        <p>Tier-1 level M&amp;A and advisory experience</p>
        <p>Highly disciplined approach to business sales</p>
      </div>
      <div class="member__profile">
        <div class="member__portrait" role="img" aria-label="Portrait photo of Adrian Korvel"></div>
        <div class="member__name">Adrian Korvel</div>
        <div class="member__credentials">B Eng, MAppFin, GAICD, FFinsia, CPEng, RPEQ</div>
      </div>
      <ul class="member__highlights">
        <li><svg class="tick" viewBox="0 0 10 10"><circle cx="5" cy="5" r="4.3" fill="none" stroke="#fff" stroke-width="1"/><path d="M2.8 5.1L4.4 6.6L7.3 3.4" fill="none" stroke="#fff" stroke-width="1.1"/></svg>&gt;25 years' international consulting, advisory experience</li>
        <li><svg class="tick" viewBox="0 0 10 10"><circle cx="5" cy="5" r="4.3" fill="none" stroke="#fff" stroke-width="1"/><path d="M2.8 5.1L4.4 6.6L7.3 3.4" fill="none" stroke="#fff" stroke-width="1.1"/></svg>Mergers, acquisitions and divestment experience</li>
        <li><svg class="tick" viewBox="0 0 10 10"><circle cx="5" cy="5" r="4.3" fill="none" stroke="#fff" stroke-width="1"/><path d="M2.8 5.1L4.4 6.6L7.3 3.4" fill="none" stroke="#fff" stroke-width="1.1"/></svg>Large bid management credentials leadings bids &gt; $500M</li>
        <li><svg class="tick" viewBox="0 0 10 10"><circle cx="5" cy="5" r="4.3" fill="none" stroke="#fff" stroke-width="1"/><path d="M2.8 5.1L4.4 6.6L7.3 3.4" fill="none" stroke="#fff" stroke-width="1.1"/></svg>Responsible manager for Australian Financial Services License</li>
      </ul>
    </article>

    <article class="member member--three">
      <div class="member__strengths">
        <h3>Breadth of expertise:</h3>
        <p>Preparation and optimisation for sale</p>
        <p>Business sales</p>
        <p>Business acquisition and roll-ups</p>
        <p>Logistics tender management</p>
        <p>Logistics contract management</p>
        <p>Professional business development</p>
        <p>Business/profit improvement</p>
      </div>
      <div class="member__profile">
        <div class="member__portrait" role="img" aria-label="Portrait photo of Stuart Brennan"></div>
        <div class="member__name">Stuart Brennan</div>
        <div class="member__credentials">CA, FCA, CEP</div>
      </div>
      <ul class="member__highlights">
        <li><svg class="tick" viewBox="0 0 10 10"><circle cx="5" cy="5" r="4.3" fill="none" stroke="#fff" stroke-width="1"/><path d="M2.8 5.1L4.4 6.6L7.3 3.4" fill="none" stroke="#fff" stroke-width="1.1"/></svg>Ex-CFO of ultra-high growth businesses</li>
        <li><svg class="tick" viewBox="0 0 10 10"><circle cx="5" cy="5" r="4.3" fill="none" stroke="#fff" stroke-width="1"/><path d="M2.8 5.1L4.4 6.6L7.3 3.4" fill="none" stroke="#fff" stroke-width="1.1"/></svg>Highly experienced in business roll-up strategies</li>
        <li><svg class="tick" viewBox="0 0 10 10"><circle cx="5" cy="5" r="4.3" fill="none" stroke="#fff" stroke-width="1"/><path d="M2.8 5.1L4.4 6.6L7.3 3.4" fill="none" stroke="#fff" stroke-width="1.1"/></svg>Completed over 25 acquisitions and implementations</li>
        <li><svg class="tick" viewBox="0 0 10 10"><circle cx="5" cy="5" r="4.3" fill="none" stroke="#fff" stroke-width="1"/><path d="M2.8 5.1L4.4 6.6L7.3 3.4" fill="none" stroke="#fff" stroke-width="1.1"/></svg>Executed divestment and merger programmes</li>
      </ul>
    </article>
  </section>

  <section class="page page--right">
    <svg class="corner-swoosh" width="180" height="95" viewBox="0 0 180 95" aria-hidden="true">
      <path d="M180 0H0C30 12 70 40 100 62C130 84 160 92 180 94Z" fill="#9aa7b0"/>
      <path d="M180 0H40C65 15 95 42 120 64C145 84 165 92 180 94Z" fill="var(--deep-blue)"/>
    </svg>
    <h2 class="route-title">AUSTRALIA TRANSPORTATION ROUTE</h2>
    <div class="route-map" role="img" aria-label="Map of Australia showing the national rail and transport routes between major cities"></div>
    <div class="warehouse-photo" role="img" aria-label="Photo of a long warehouse aisle with tall racks of stacked cartons"></div>
    <p class="site-address">www. southlinklog.com.au</p>
  </section>
</div>
</body>
</html>
```